Reproduce my app screenshot to look more updated and modern

My app is a place for farmers to post jobs a when needing help around the Farm, and local farmhands can apply for the job. The Farmer can then review multiple applicants and select the one best fit for the task at hand. I'm trying to give my screens an updated look while keeping my current color scheme and flow. I would like for you guys to recreate this screen with an updated loo the best you can. The main screen with the KT will stay the same. I put that in there to show our logo and our main colors. They look outdated.

Target Market(s)

Farmers and Farm Emlpoyees inside the US

Industry/Entity Type

Agriculture

Requirements
Must have
• and updated look and same buttom/ functionality
Nice to have
Should not have
• dont change the name of any buttons

```html
<!DOCTYPE html>
<html lang="en">
<head>
<meta charset="utf-8">
<title>FieldCrew – App Screens</title>
<link href="https://fonts.googleapis.com/css2?family=Outfit:wght@300;400;500;600;700&display=swap" rel="stylesheet">
<style>
  :root{
    --stage:#0a3319;
    --lime:#b8ef60;
    --lime-soft:#eef9dc;
    --lime-deep:#86cc32;
    --brand:#25893f;
    --brand-dark:#17642c;
    --accent:#5fae1f;
    --ink:#142015;
    --body:#4d564e;
    --muted:#98a098;
    --line:#e6ebe4;
    --card:#ffffff;
    --surface:#f3f6f1;
    --chip:#eef2ec;
    --field-mid:#6fbf3a;
    --field-low:#2a7024;
  }
  *{box-sizing:border-box;margin:0;padding:0}
  html,body{width:1200px;height:700px;overflow:hidden;background:var(--stage)}
  body{font-family:"Outfit",sans-serif;color:var(--ink);position:relative}

  .screen{position:absolute;width:344px;overflow:hidden;background:var(--surface);border-radius:18px}
  .screen--splash{left:44px;top:44px;height:611px;background:var(--lime)}
  .screen--list{left:428px;top:0;height:333px;border-radius:0 0 18px 18px}
  .screen--launch{left:429px;top:364px;height:336px;background:var(--lime);border-radius:18px 18px 0 0}
  .screen--home{left:815px;top:42px;height:611px}

  /* splash + launch */
  .field-photo{position:absolute;left:0;right:0;bottom:0;height:340px;
    background:linear-gradient(180deg,rgba(184,239,96,0) 0%,var(--field-mid) 45%,var(--field-low) 100%)}
  .screen--launch .field-photo{height:200px;opacity:.55}
  .app-mark{position:absolute;width:112px;height:112px;border-radius:30px;background:var(--brand);
    display:flex;align-items:center;justify-content:center;color:#fff;font-weight:700;font-size:42px;
    box-shadow:0 14px 30px rgba(10,51,25,.28)}
  .screen--splash .app-mark{left:116px;top:280px}
  .screen--launch .app-mark{left:116px;top:246px}
  .splash-name{position:absolute;left:0;right:0;top:556px;text-align:center;color:#fff;font-weight:700;font-size:30px;letter-spacing:.3px}

  /* home header */
  .home-header{position:absolute;left:0;top:0;width:344px;height:100px;border-radius:0 0 22px 22px;
    background:linear-gradient(135deg,#2a9645,var(--brand-dark))}
  .brand-name{position:absolute;left:0;right:0;top:16px;text-align:center;color:#fff;font-weight:600;font-size:15px;letter-spacing:2px}
  .menu-btn{position:absolute;left:308px;top:20px;width:18px;height:13px}
  .avatar{position:absolute;left:18px;top:50px;width:34px;height:34px;border-radius:50%;background:#dfe9dc;border:2px solid rgba(255,255,255,.7)}
  .user-name{position:absolute;left:62px;top:52px;color:#fff;font-size:12px;font-weight:600}
  .user-phone{position:absolute;left:62px;top:69px;color:var(--lime);font-size:9.5px}
  .edit-btn{position:absolute;left:236px;top:55px;width:92px;height:26px;border-radius:13px;background:var(--lime);
    color:var(--brand-dark);font-size:10px;font-weight:600;display:flex;align-items:center;justify-content:center}

  .post-btn{position:absolute;left:16px;top:110px;width:312px;height:30px;border-radius:15px;background:var(--brand);
    color:#fff;font-size:10.5px;font-weight:600;letter-spacing:.8px;display:flex;align-items:center;justify-content:center;gap:8px;
    box-shadow:0 6px 14px rgba(37,137,63,.25)}
  .tabs{position:absolute;left:16px;top:148px;width:312px;height:32px;border-radius:16px;background:#e4eae1;padding:3px;display:flex}
  .tab{flex:1;display:flex;align-items:center;justify-content:center;font-size:11px;font-weight:500;color:var(--body);border-radius:13px}
  .tab--active{background:var(--lime);color:var(--brand-dark);font-weight:600}
  .search{position:absolute;left:16px;top:190px;width:236px;height:32px;border-radius:16px;background:#fff;
    font-size:10.5px;color:var(--muted);padding-left:12px;display:flex;align-items:center;gap:8px}
  .filter{position:absolute;left:260px;top:190px;width:68px;height:32px;border-radius:16px;background:#fff;
    font-size:10.5px;color:var(--body);display:flex;align-items:center;justify-content:center;gap:7px}

  /* job cards */
  .job-card{position:absolute;left:16px;width:312px;height:104px;background:var(--card);border-radius:16px;
    box-shadow:0 4px 14px rgba(20,60,25,.06)}
  .job-title{position:absolute;left:16px;top:13px;font-size:13.5px;font-weight:600}
  .fav{position:absolute;right:12px;top:10px;width:28px;height:28px;border-radius:50%;background:var(--chip);
    display:flex;align-items:center;justify-content:center}
  .fav svg{width:14px;height:13px;fill:none;stroke:#8a938a;stroke-width:1.6}
  .fav--on{background:var(--lime-soft)}
  .fav--on svg{fill:var(--lime-deep);stroke:var(--lime-deep)}
  .pay{position:absolute;left:16px;top:35px;display:flex;align-items:center;gap:7px;font-size:12px;font-weight:600;color:var(--brand-dark)}
  .meta,.foot{position:absolute;left:16px;display:flex;align-items:center;gap:16px}
  .meta{top:57px;font-size:10.5px;color:var(--body)}
  .foot{top:84px;font-size:9.5px;color:var(--body)}
  .item{display:flex;align-items:center;gap:5px;white-space:nowrap}
  .item--green{color:var(--accent);font-weight:500}
  .pay svg,.item svg{width:13px;height:13px;flex:none}
  .divider{position:absolute;left:16px;right:16px;top:77px;border-top:1px dashed var(--line)}
  .fab{position:absolute;width:44px;height:44px;border-radius:50%;background:var(--lime);
    display:flex;align-items:center;justify-content:center;box-shadow:0 8px 18px rgba(60,120,20,.3)}
  .fab svg{width:19px;height:17px;fill:#fff}

  /* tab bar */
  .tab-bar{position:absolute;left:12px;width:320px;height:42px;background:#fff;border-radius:16px;
    box-shadow:0 6px 20px rgba(20,60,25,.1);display:flex;justify-content:space-around;align-items:center}
  .nav-item{width:40px;height:30px;border-radius:10px;display:flex;align-items:center;justify-content:center}
  .nav-item--active{background:var(--lime-soft)}
  .nav-item svg{width:20px;height:20px}
  .icon-line{fill:none;stroke:var(--ink);stroke-width:1.6;stroke-linecap:round;stroke-linejoin:round}
  .icon-soft{fill:none;stroke:#7f887f;stroke-width:1.3;stroke-linecap:round;stroke-linejoin:round}
</style>
</head>
<body>
<svg width="0" height="0" style="position:absolute" aria-hidden="true">
  <symbol id="i-bag" viewBox="0 0 16 16"><path fill="none" stroke="currentColor" stroke-width="1.3" stroke-linecap="round" stroke-linejoin="round" d="M6 2h4l-1 2.5H7zM7 4.5C4 6 3 9 3 11c0 2 1.5 3 5 3s5-1 5-3c0-2-1-5-4-6.5M8 7.5v4M9.2 8.4c-.4-.5-2.4-.6-2.4.5s2.4.6 2.4 1.7-2 1-2.4.4"/></symbol>
  <symbol id="i-pin" viewBox="0 0 16 16"><path class="icon-soft" d="M8 14.5s-4.5-4.6-4.5-8a4.5 4.5 0 0 1 9 0c0 3.4-4.5 8-4.5 8z"/><circle class="icon-soft" cx="8" cy="6.5" r="1.6"/></symbol>
  <symbol id="i-clock" viewBox="0 0 16 16"><circle fill="none" stroke="currentColor" stroke-width="1.3" cx="8" cy="8" r="6.3"/><path fill="none" stroke="currentColor" stroke-width="1.3" stroke-linecap="round" d="M8 4.5V8h3"/></symbol>
  <symbol id="i-route" viewBox="0 0 16 16"><path class="icon-soft" d="M4 13.5S1.5 11 1.5 9a2.5 2.5 0 0 1 5 0c0 2-2.5 4.5-2.5 4.5zM13 6s-1.6-1.6-1.6-2.9a1.6 1.6 0 0 1 3.2 0C14.6 4.4 13 6 13 6zM7 13.5c3 0 5-1 4-3s-3-1-2-3 3-1 3-1"/></symbol>
  <symbol id="i-case" viewBox="0 0 16 16"><rect fill="none" stroke="currentColor" stroke-width="1.3" x="1.5" y="4.5" width="13" height="9" rx="1.5"/><path fill="none" stroke="currentColor" stroke-width="1.3" d="M6 4.5V3h4v1.5M1.5 8.5h13"/></symbol>
  <symbol id="i-heart" viewBox="0 0 20 18"><path d="M10 16.5S1.5 11.2 1.5 5.6A4.1 4.1 0 0 1 10 3.8a4.1 4.1 0 0 1 8.5 1.8c0 5.6-8.5 10.9-8.5 10.9z"/></symbol>
  <symbol id="i-home" viewBox="0 0 24 24"><path d="M3 11 12 3l9 8h-3v9h-4v-6h-4v6H6v-9z" fill="var(--lime-deep)"/></symbol>
  <symbol id="i-search" viewBox="0 0 24 24"><circle class="icon-line" cx="10" cy="10" r="6.5"/><path class="icon-line" d="m15 15 6 6"/></symbol>
  <symbol id="i-list" viewBox="0 0 24 24"><path class="icon-line" d="M13 21H5V3h14v10M8 8h8M8 12h8M8 16h4M14 19l2 2 5-5"/></symbol>
  <symbol id="i-hand" viewBox="0 0 24 24"><path class="icon-line" d="M2 17h4l4 2h6l6-4-2-1-5 2h-4M6 17l3-3h5M15 11c0-4 3-6 6-7-1 4-3 6-6 7zM15 11V8"/></symbol>
  <symbol id="i-cal" viewBox="0 0 24 24"><rect class="icon-line" x="3" y="5" width="18" height="16" rx="3"/><path class="icon-line" d="M3 9h18M8 3v4M16 3v4"/><text x="12" y="18.5" text-anchor="middle" font-family="Outfit,sans-serif" font-size="8" font-weight="700" fill="var(--ink)">15</text></symbol>
</svg>

<!-- Splash screen -->
<section class="screen screen--splash">
  <div class="field-photo" role="img" aria-label="Young corn rows in a misty field"></div>
  <div class="app-mark">KT</div>
  <div class="splash-name">FieldCrew</div>
</section>

<!-- Scrolled job list -->
<section class="screen screen--list">
  <article class="job-card" style="top:-64px">
    <div class="foot">
      <span class="item"><svg><use href="#i-route"/></svg>2.92miles</span>
      <span class="item item--green"><svg><use href="#i-case"/></svg>Apr 1 - Dec 15</span>
    </div>
  </article>
  <article class="job-card" style="top:48px">
    <h3 class="job-title">Truck Driver</h3>
    <span class="fav fav--on"><svg><use href="#i-heart"/></svg></span>
    <div class="pay"><svg><use href="#i-bag"/></svg>$ 12 - 20 per hour</div>
    <div class="meta">
      <span class="item"><svg><use href="#i-pin"/></svg>Dewitt, Iowa</span>
      <span class="item item--green"><svg><use href="#i-clock"/></svg>3pm - 3pm</span>
    </div>
    <div class="divider"></div>
    <div class="foot">
      <span class="item"><svg><use href="#i-route"/></svg>2.92miles</span>
      <span class="item item--green"><svg><use href="#i-case"/></svg>Mar 01 - Feb 28</span>
    </div>
  </article>
  <article class="job-card" style="top:160px">
    <h3 class="job-title">Farm Hand, Sprayer, Truck, Repair</h3>
    <span class="fav"><svg><use href="#i-heart"/></svg></span>
    <div class="pay"><svg><use href="#i-bag"/></svg>$ 16 - 22 per hour</div>
    <div class="meta">
      <span class="item"><svg><use href="#i-pin"/></svg>Dewitt, Iowa</span>
      <span class="item item--green"><svg><use href="#i-clock"/></svg>1am - 1am</span>
    </div>
    <div class="divider"></div>
    <div class="foot">
      <span class="item"><svg><use href="#i-route"/></svg>6.09miles</span>
      <span class="item item--green"><svg><use href="#i-case"/></svg>Jan 31 - Dec 31</span>
    </div>
  </article>
  <div class="fab" style="left:278px;top:216px"><svg><use href="#i-heart"/></svg></div>
  <nav class="tab-bar" style="top:283px">
    <span class="nav-item nav-item--active"><svg><use href="#i-home"/></svg></span>
    <span class="nav-item"><svg><use href="#i-search"/></svg></span>
    <span class="nav-item"><svg><use href="#i-list"/></svg></span>
    <span class="nav-item"><svg><use href="#i-hand"/></svg></span>
    <span class="nav-item"><svg><use href="#i-cal"/></svg></span>
  </nav>
</section>

<!-- Launch screen -->
<section class="screen screen--launch">
  <div class="field-photo" role="img" aria-label="Misty cornfield fading into green"></div>
  <div class="app-mark">KT</div>
</section>

<!-- Home screen -->
<section class="screen screen--home">
  <header class="home-header">
    <div class="brand-name">FIELDCREW</div>
    <svg class="menu-btn" viewBox="0 0 18 13"><path d="M0 1h18M0 6.5h18M6 12h12" stroke="#fff" stroke-width="1.6" stroke-linecap="round"/></svg>
    <div class="avatar"></div>
    <div class="user-name">Daniel Hartwell</div>
    <div class="user-phone">5550147829</div>
    <div class="edit-btn">Edit Details</div>
  </header>
  <div class="post-btn">
    <svg width="10" height="10" viewBox="0 0 10 10"><path d="M5 1v8M1 5h8" stroke="#fff" stroke-width="1.6" stroke-linecap="round"/></svg>
    POST NEW JOB
  </div>
  <div class="tabs">
    <div class="tab tab--active">Current Jobs For You</div>
    <div class="tab">Nearby Farmlands</div>
  </div>
  <div class="search">
    <svg width="13" height="13" viewBox="0 0 24 24"><circle cx="10" cy="10" r="6.5" fill="none" stroke="#98a098" stroke-width="2"/><path d="m15 15 6 6" stroke="#98a098" stroke-width="2" stroke-linecap="round"/></svg>
    Search Jobs, Farmhands
  </div>
  <div class="filter">Filter
    <svg width="13" height="12" viewBox="0 0 13 12"><path d="M0 2h13M0 6h13M0 10h13" stroke="#4d564e" stroke-width="1"/><circle cx="4" cy="2" r="1.5" fill="#fff" stroke="#4d564e"/><circle cx="9" cy="6" r="1.5" fill="#fff" stroke="#4d564e"/><circle cx="5" cy="10" r="1.5" fill="#fff" stroke="#4d564e"/></svg>
  </div>

  <article class="job-card" style="top:232px">
    <h3 class="job-title">Seasonal Farm Labor</h3>
    <span class="fav"><svg><use href="#i-heart"/></svg></span>
    <div class="pay"><svg><use href="#i-bag"/></svg>$ 12 - 20 per hour</div>
    <div class="meta">
      <span class="item"><svg><use href="#i-pin"/></svg>Dewitt, Iowa</span>
      <span class="item item--green"><svg><use href="#i-clock"/></svg>8am - 8am</span>
    </div>
    <div class="divider"></div>
    <div class="foot">
      <span class="item"><svg><use href="#i-route"/></svg>2.92miles</span>
      <span class="item item--green"><svg><use href="#i-case"/></svg>Apr 1 - Dec 15</span>
    </div>
  </article>
  <article class="job-card" style="top:344px">
    <h3 class="job-title">Truck Driver</h3>
    <span class="fav fav--on"><svg><use href="#i-heart"/></svg></span>
    <div class="pay"><svg><use href="#i-bag"/></svg>$ 12 - 20 per hour</div>
    <div class="meta">
      <span class="item"><svg><use href="#i-pin"/></svg>Dewitt, Iowa</span>
      <span class="item item--green"><svg><use href="#i-clock"/></svg>3pm - 3pm</span>
    </div>
    <div class="divider"></div>
    <div class="foot">
      <span class="item"><svg><use href="#i-route"/></svg>2.92miles</span>
      <span class="item item--green"><svg><use href="#i-case"/></svg>Mar 01 - Feb 28</span>
    </div>
  </article>
  <article class="job-card" style="top:456px">
    <h3 class="job-title">Farm Hand, Sprayer, Truck, Repair</h3>
    <span class="fav"><svg><use href="#i-heart"/></svg></span>
    <div class="pay"><svg><use href="#i-bag"/></svg>$ 16 - 22 per hour</div>
    <div class="meta">
      <span class="item"><svg><use href="#i-pin"/></svg>Dewitt, Iowa</span>
      <span class="item item--green"><svg><use href="#i-clock"/></svg>1am - 1am</span>
    </div>
    <div class="divider"></div>
    <div class="foot">
      <span class="item"><svg><use href="#i-route"/></svg>6.09miles</span>
      <span class="item item--green"><svg><use href="#i-case"/></svg>Jan 31 - Dec 31</span>
    </div>
  </article>
  <div class="fab" style="left:278px;top:510px"><svg><use href="#i-heart"/></svg></div>

  <nav class="tab-bar" style="top:563px">
    <span class="nav-item nav-item--active"><svg><use href="#i-home"/></svg></span>
    <span class="nav-item"><svg><use href="#i-search"/></svg></span>
    <span class="nav-item"><svg><use href="#i-list"/></svg></span>
    <span class="nav-item"><svg><use href="#i-hand"/></svg></span>
    <span class="nav-item"><svg><use href="#i-cal"/></svg></span>
  </nav>
</section>
</body>
</html>
```